Design a Book Cover for Veltrix Development Book

I need to create an eBook design for a technical book with the following info.
Title: Brisko Veltrix - Grow Into A Veltrix Builder in 90 Sprints!
Subtitle: Learn how to Build 10 Complete Veltrix Apps with Marzel.
Author: Teo Brannick
Delivery should include all book cover formats, 2D, 3D, Kindle, Print, etc.
Target Market(s)
People who want to learn Veltrix development, people who want to switch careers to programming.
Industry/Entity Type
Programming
Colors
fec214
0792cd
ec1f27
Requirements
Should not have
- Do not use Veltrix logo (green robot), Do not use Marzel logo (K).

```html
<!DOCTYPE html>
<html lang="en">
<head>
<meta charset="utf-8">
<title>Brisko Veltrix – Book Cover</title>
<link rel="stylesheet" href="https://fonts.googleapis.com/css2?family=Comfortaa:wght@700&family=Montserrat:wght@500;800&display=swap">
<style>
  :root {
    --backdrop: #616161;
    --cover-white: #f2f2f0;
    --brand-green: #5e9c2c;
    --tagline-grey: #8a8a8a;
    --on-green: #f2f2f0;
  }
  * { box-sizing: border-box; margin: 0; padding: 0; }
  html, body {
    width: 1200px; height: 1200px; overflow: hidden;
    background: var(--backdrop);
  }
  .book-cover {
    position: absolute;
    left: 244px; top: 40px;
    width: 713px; height: 1120px;
    background: var(--cover-white);
    overflow: hidden;
    box-shadow: 0 20px 40px rgba(0,0,0,0.25);
  }
  .title {
    position: absolute;
    left: 0; right: 0; top: 130px;
    text-align: center;
    font-family: "Comfortaa", sans-serif;
    font-weight: 700;
    font-size: 128px;
    line-height: 112px;
    letter-spacing: -3px;
    color: var(--brand-green);
  }
  .title span { display: block; }
  .tagline {
    position: absolute;
    left: 0; right: 0; top: 420px;
    text-align: center;
    font-family: "Montserrat", sans-serif;
    color: var(--tagline-grey);
  }
  .tagline-lead {
    font-weight: 500;
    font-size: 19px;
    letter-spacing: 0.5px;
  }
  .tagline-promise {
    font-weight: 800;
    font-size: 60px;
    line-height: 64px;
    letter-spacing: 0.5px;
  }
  .green-arc {
    position: absolute;
    left: 0; top: 0;
    width: 713px; height: 1120px;
  }
  .green-arc circle { fill: var(--brand-green); }
  .subtitle {
    position: absolute;
    left: 0; right: 0; top: 932px;
    text-align: center;
    font-family: "Montserrat", sans-serif;
    font-weight: 500;
    font-size: 16px;
    line-height: 21px;
    letter-spacing: 0.6px;
    color: var(--on-green);
  }
  .author {
    position: absolute;
    left: 0; right: 0; top: 1008px;
    text-align: center;
    font-family: "Montserrat", sans-serif;
    font-weight: 800;
    font-size: 52px;
    letter-spacing: 1px;
    color: var(--on-green);
  }
</style>
</head>
<body>
  <main class="book-cover">
    <svg class="green-arc" viewBox="0 0 713 1120" aria-hidden="true">
      <circle cx="356.5" cy="1208.5" r="446.5"/>
    </svg>
    <h1 class="title"><span>brisko</span><span>veltrix</span></h1>
    <div class="tagline">
      <p class="tagline-lead">GROW INTO A VELTRIX BUILDER IN</p>
      <p class="tagline-promise">90 SPRINTS!</p>
    </div>
    <p class="subtitle">LEARN HOW TO BUILD 10 COMPLETE<br>VELTRIX APPS WITH MARZEL.</p>
    <p class="author">TEO BRANNICK</p>
  </main>
</body>
</html>
```